I want a website to be designed for our new company, it's an import and export company for variety of things.

please see the attached Logo for our company and the Images for our different sections for our busienss

Target Market(s)

multiple

Coding

Coded - Design and coding required

Number of Pages Required

5+ page

Font styles to use
Sans Serif

Colors

Designer to choose colors to be used in the design.

Requirements
Must have
• KVR GLOBALINKS
• KVR globalinks Trading & Contracting provides various services. The Company offers infrastructure construction, oil, enegy and gas services, agricultural projects, real estate development, travel and tourism, and food processing and trading.
• Civil contracting for infrastructure, residential and heavy projects. Through its main subsidiaries; distribution of general food products, construction chemicals including corrosion inhibitors and electrical machinery; provides catering and travel agency services; ownership and operation of a school; offers human sources services including manpower supply.
• Drilling and Gold Mines Used Machinery, All Kinds of Construction Machinery, Drilling Machines are manufactured and sold.
Nice to have
• good designa and beautiful colours, it has too look professional

```html
<!DOCTYPE html>
<html lang="en">
<head>
<meta charset="utf-8">
<title>KVR Globalinks — Trading &amp; Contracting</title>
<link href="https://fonts.googleapis.com/css2?family=Montserrat:wght@500;600;700;800&family=Lato:wght@400;700&display=swap" rel="stylesheet">
<style>
:root{
  --gold:#b07a2a;
  --olive:#8c6c1c;
  --green:#2f4a1f;
  --green-band:#3c5a2b;
  --ink:#1c1c1c;
  --dark:#161616;
  --darker:#0f0f0f;
  --text:#4a4a4a;
  --navy:#1e2f5a;
  --grey-bg:#ececec;
  --white:#fff;
}
*{margin:0;padding:0;box-sizing:border-box}
html,body{width:1200px;height:4518px;overflow:hidden;background:#fff}
body{font-family:"Lato",sans-serif;color:var(--text);position:relative}
.abs{position:absolute}
section,header,footer{position:absolute;left:0;width:1200px}
.h-title{font-family:"Montserrat",sans-serif;font-weight:800;color:var(--ink);font-size:29px;letter-spacing:.3px;text-align:center;width:1200px;left:0}
.h-title span{color:var(--gold)}
.btn{position:absolute;background:var(--green);color:#fff;font-family:"Montserrat",sans-serif;font-weight:700;font-size:16px;letter-spacing:.5px;display:flex;align-items:center;justify-content:center;border-radius:2px}
.lead{font-size:15px;line-height:27px;color:var(--text)}
/* header */
.site-header{top:0;height:147px;background:var(--ink)}
.topbar{top:0;height:49px;width:1200px;border-bottom:1px solid #2a2a2a}
.phone{left:74px;top:13px;color:#fff;font-size:17px;display:flex;align-items:center;gap:14px}
.social{display:flex;gap:19px}
.social i{display:block;width:22px;height:22px;border-radius:50%;border:2px solid #fff}
.nav a{position:absolute;top:92px;color:#fff;font-family:"Montserrat",sans-serif;font-weight:600;font-size:14px;text-decoration:none}
.nav a.active{color:var(--gold)}
.logo-plate{left:484px;top:0;width:232px;height:140px;background:#0d0d0d;clip-path:polygon(0 0,100% 0,92% 100%,8% 100%)}
.brand{display:flex;align-items:center;gap:10px;font-family:"Montserrat",sans-serif;font-weight:600;color:#fff;letter-spacing:2px}
.brand i{display:block;border-radius:50%;border:2px solid #fff}
/* hero */
.hero{top:147px;height:574px;background:linear-gradient(180deg,#2f5f9a 0%,#6c91bd 30%,#b7c4cf 48%,#6d5f52 66%,#3f3a33 85%,#2b2722 100%)}
.hero h1{position:absolute;left:0;width:1200px;top:234px;text-align:center;font-family:"Montserrat",sans-serif;font-weight:700;color:#fff;font-size:49px;line-height:51px;letter-spacing:.5px}
.dots{left:562px;top:529px;display:flex;gap:16px}
.dots i{width:12px;height:12px;border-radius:50%;background:#fff}
.dots i:first-child{background:var(--gold)}
/* about */
.about{top:721px;height:458px}
.sec-h{font-family:"Montserrat",sans-serif;font-weight:800;font-size:29px;line-height:33px;color:var(--ink)}
.sec-h span{color:var(--gold)}
/* services */
.services{top:1179px;height:747px;background:radial-gradient(ellipse at 50% 55%,#fbfbfb 0%,#eeeeee 55%,#e2e2e2 100%)}
.svc h3{font-family:"Montserrat",sans-serif;font-weight:700;font-size:18px;color:var(--olive);margin-bottom:6px}
.svc p{font-size:15px;line-height:23px}
.svc.r{text-align:right}
.ic{position:absolute;width:78px;height:78px;border-radius:50%;background:#fff;box-shadow:0 2px 8px rgba(0,0,0,.15);display:flex;align-items:center;justify-content:center}
.ic.on{background:var(--gold)}
/* projects */
.projects{top:1926px;height:595px}
.card{position:absolute;top:134px;width:331px;text-align:center}
.card .ph{height:212px}
.card h3{font-family:"Montserrat",sans-serif;font-weight:700;font-size:18px;color:var(--green);margin-top:28px}
.card p{font-size:15px;line-height:23px;margin-top:5px}
/* chairman */
.chair{top:2521px;height:479px;background:var(--grey-bg)}
/* blog */
.blog{top:3000px;height:514px}
.post{position:absolute;width:520px;height:130px}
.post .ph{position:absolute;left:0;top:0;width:180px;height:130px}
.post .tx{position:absolute;left:196px;top:2px;width:340px}
.post .d{font-family:"Montserrat",sans-serif;font-weight:600;font-size:13px;color:var(--olive)}
.post h4{font-family:"Montserrat",sans-serif;font-weight:700;font-size:18px;color:var(--green);margin:4px 0 4px}
.post p{font-size:15px;line-height:26px}
/* reviews */
.reviews{top:3514px;height:525px;background:linear-gradient(180deg,#e6e6e6,#f2f2f2 40%,#f2f2f2)}
.person{position:absolute;top:309px;width:140px;text-align:center}
.person .av{width:98px;height:98px;border-radius:50%;margin:0 auto;background:linear-gradient(160deg,#d9d9d9,#8b8b8b)}
.person h5{font-family:"Montserrat",sans-serif;font-weight:700;font-size:14px;color:var(--ink);margin-top:14px}
.person small{display:block;font-size:14px;color:#666;margin-top:2px}
/* newsletter */
.news{top:4039px;height:87px;background:var(--green-band)}
.news-title{left:75px;top:32px;font-family:"Montserrat",sans-serif;font-weight:700;font-size:19px;color:#fff;white-space:nowrap}
/* footer */
.foot{top:4126px;height:330px;background:var(--ink);color:#ddd}
.foot h6{font-family:"Montserrat",sans-serif;font-weight:600;font-size:16px;color:#fff;letter-spacing:.3px}
.foot ul{list-style:none;margin-top:12px}
.foot li{font-size:14px;line-height:30.7px;color:#ddd}
.copy{top:4456px;height:62px;background:var(--darker);color:#ddd;font-size:14px;display:flex;align-items:center;justify-content:center}
</style>
</head>
<body>

<header class="site-header">
  <div class="topbar abs">
    <div class="phone abs">
      <svg width="14" height="14" viewBox="0 0 24 24"><path fill="#b07a2a" d="M6.6 10.8a15 15 0 0 0 6.6 6.6l2.2-2.2c.3-.3.7-.4 1-.2 1.1.4 2.3.6 3.6.6.6 0 1 .4 1 1V20c0 .6-.4 1-1 1A17 17 0 0 1 3 4c0-.6.4-1 1-1h3.5c.6 0 1 .4 1 1 0 1.3.2 2.5.6 3.6.1.3 0 .7-.2 1z"/></svg>
      <span>+90 312 555 0140,&nbsp; +90 312 555 0141</span>
    </div>
    <div class="social abs" style="left:930px;top:13px" aria-label="Social links"><i></i><i></i><i></i><i></i><i></i></div>
  </div>
  <div class="logo-plate abs"></div>
  <div class="brand abs" style="left:514px;top:58px;font-size:15px"><i style="width:18px;height:18px"></i>KVR GLOBALINKS</div>
  <nav class="nav">
    <a class="active" style="left:109px">HOME</a>
    <a style="left:205px">ABOUT US</a>
    <a style="left:329px">OUR SERVICES</a>
    <a style="left:767px">PROJECTS</a>
    <a style="left:891px">BLOG</a>
    <a style="left:979px">CONTACT US</a>
  </nav>
</header>

<section class="hero" role="img" aria-label="Red drilling rig on rocky ground under a blue cloudy sky">
  <h1>DRILLING MACHINES<br>ARE MANUFACTURED AND SOLD</h1>
  <div class="dots abs"><i></i><i></i><i></i></div>
</section>

<section class="about">
  <h2 class="sec-h abs" style="left:74px;top:66px">ABOUT <span>KVR TRADING<br>&amp; CONTRACTING COMPANY</span></h2>
  <p class="lead abs" style="left:74px;top:148px;width:600px">KVR globalinks Trading &amp; Contracting provides various services. The Company offers infrastructure construction, oil, enegy and gas services, agricultural projects, real estate development, travel and tourism, and food processing and trading.</p>
  <p class="lead abs" style="left:74px;top:237px;width:600px">Civil contracting for infrastructure, residential and heavy projects. Through its main subsidiaries; distribution of general food products, construction chemicals including corrosion inhibitors and electrical machinery.</p>
  <div class="btn" style="left:74px;top:337px;width:181px;height:44px">READ MORE</div>
  <div class="abs" style="left:704px;top:67px;width:422px;height:312px;background:var(--navy)"></div>
  <div class="abs" role="img" aria-label="Businessman in a dark suit holding a glowing world map" style="left:697px;top:77px;width:422px;height:308px;background:linear-gradient(135deg,#5a5f66,#2a2d31 60%,#1a1b1d)"></div>
</section>

<section class="services">
  <h2 class="h-title abs" style="top:60px">OUR <span>SERVICES</span></h2>
  <svg class="abs" style="left:0;top:0" width="1200" height="747">
    <circle cx="600" cy="363" r="203" fill="none" stroke="#999" stroke-width="1.5" stroke-dasharray="6 6"/>
    <circle cx="600" cy="363" r="153" fill="#151515"/>
  </svg>
  <div class="brand abs" style="left:468px;top:351px;font-size:18px;width:264px;justify-content:center"><i style="width:20px;height:20px"></i>KVR GLOBALINKS</div>

  <div class="ic" style="left:431px;top:168px"><svg width="34" height="34" viewBox="0 0 24 24" fill="none" stroke="#b07a2a" stroke-width="1.8"><rect x="4" y="10" width="16" height="10"/><path d="M4 10l8-6 8 6"/></svg></div>
  <div class="ic on" style="left:705px;top:168px"><svg width="34" height="34" viewBox="0 0 24 24" fill="none" stroke="#fff" stroke-width="2"><path d="M5 19c8 0 14-6 14-14C11 5 5 11 5 19zM5 19l8-8"/></svg></div>
  <div class="ic" style="left:363px;top:324px"><svg width="34" height="34" viewBox="0 0 24 24" fill="none" stroke="#b07a2a" stroke-width="1.8"><path d="M4 20h16M6 20V10h4v10M14 20V6h4v14"/></svg></div>
  <div class="ic" style="left:766px;top:324px"><svg width="30" height="30" viewBox="0 0 24 24"><path fill="#b07a2a" d="M21 16v-2l-8-5V3.5a1.5 1.5 0 0 0-3 0V9l-8 5v2l8-2.5V19l-2 1.5V22l3.5-1 3.5 1v-1.5L13 19v-5.5z"/></svg></div>
  <div class="ic" style="left:431px;top:479px"><svg width="34" height="34" viewBox="0 0 24 24" fill="none" stroke="#b07a2a" stroke-width="1.8"><path d="M12 3v17M8 20h8M6 8l6-5 6 5"/></svg></div>
  <div class="ic" style="left:705px;top:479px"><svg width="30" height="30" viewBox="0 0 24 24"><path fill="#b07a2a" d="M12 3l10 9h-3v8h-5v-6h-4v6H5v-8H2z"/></svg></div>

  <div class="svc r abs" style="left:70px;top:156px;width:335px"><h3>INFRASTRUCTURE CONSTRUCTION</h3><p>Lorem ipsum dolor sit amet, consectetur adipiscing elit interdum massa sapien se fringilla sem blandit ac.</p></div>
  <div class="svc abs" style="left:797px;top:156px;width:300px"><h3>AGRICULTURAL PROJECTS</h3><p>Lorem ipsum dolor sit amet, consectetur adipiscing elit interdum massa sapien se fringilla sem blandit ac.</p></div>
  <div class="svc r abs" style="left:94px;top:321px;width:250px"><h3>OIL</h3><p>Lorem ipsum dolor sit amet, consectetur adipiscing elit interdu mmassa sapien se fringilla</p></div>
  <div class="svc abs" style="left:860px;top:305px;width:270px"><h3>TRAVEL AND TOURISM</h3><p>Lorem ipsum dolor sit amet, consectetur adipiscing elit interdum massa sapien se fringilla sem blandit ac.</p></div>
  <div class="svc r abs" style="left:90px;top:477px;width:315px"><h3>ENEGY AND GAS SERVICES</h3><p>Lorem ipsum dolor sit amet, consectetur adipiscing elit interdum massa sapien se fringilla sem blandit ac.</p></div>
  <div class="svc abs" style="left:797px;top:477px;width:300px"><h3>REAL ESTATE DEVELOPMENT</h3><p>Lorem ipsum dolor sit amet, consectetur adipiscing elit interdum massa sapien se fringilla sem blandit ac.</p></div>

  <div class="btn" style="left:488px;top:639px;width:225px;height:42px">VIEW ALL SERVICES</div>
</section>

<section class="projects">
  <h2 class="h-title abs" style="top:68px">OUR <span>PROJECTS</span></h2>
  <div class="card" style="left:74px"><div class="ph" role="img" aria-label="Yellow drilling machine in a snowy forest" style="background:linear-gradient(180deg,#7d96a6,#5d6f6a 55%,#c9cfcf)"></div><h3>PROJECT HEADING</h3><p>Lorem ipsum dolor sit amet, consectetur<br>adipiscing elit interdum.</p><div class="btn" style="left:76px;top:347px;width:179px;height:40px">READ MORE</div></div>
  <div class="card" style="left:435px"><div class="ph" role="img" aria-label="Aerial view of a large building complex under construction" style="background:linear-gradient(180deg,#8a9098,#a9a49a 50%,#7e7a70)"></div><h3>PROJECT HEADING</h3><p>Lorem ipsum dolor sit amet, consectetur<br>adipiscing elit interdum.</p><div class="btn" style="left:76px;top:347px;width:179px;height:40px">READ MORE</div></div>
  <div class="card" style="left:797px"><div class="ph" role="img" aria-label="Offshore oil platform at sea" style="background:linear-gradient(180deg,#3f5562,#2c4250 50%,#1f3440)"></div><h3>PROJECT HEADING</h3><p>Lorem ipsum dolor sit amet, consectetur<br>adipiscing elit interdum.</p><div class="btn" style="left:76px;top:347px;width:179px;height:40px">READ MORE</div></div>
</section>

<section class="chair">
  <div class="abs" style="left:74px;top:81px;width:426px;height:309px;background:var(--navy)"></div>
  <div class="abs" role="img" aria-label="Portrait of the chairman in a suit in a modern office" style="left:82px;top:91px;width:425px;height:307px;background:linear-gradient(120deg,#dfe3e8,#9aa6b4 50%,#34405a)"></div>
  <h2 class="sec-h abs" style="left:533px;top:81px">CHAIRMAN <span>OF<br>THE BOARD MESSAGE</span></h2>
  <p class="lead abs" style="left:533px;top:160px;width:580px">The underlying principle governing the operations of KVR Globalinks Trading Company Limited is 'Your Service Partner', the common trait enabling us to consistently deliver our value promise to our customers, partners, employees and other stakeholders. As a privately owned and diversified service company, our strength is the result of an ever-widening range of activities conducted through a number of strategic business divisions.</p>
  <div class="btn" style="left:533px;top:351px;width:179px;height:42px">READ MORE</div>
</section>

<section class="blog">
  <h2 class="h-title abs" style="top:64px">BLOG <span>POSTS</span></h2>
  <div class="post" style="left:74px;top:133px"><div class="ph" role="img" aria-label="Workers at a sunlit industrial site" style="background:linear-gradient(135deg,#c9a77a,#6e6a66)"></div><div class="tx"><div class="d">JANUARY 18, 2019</div><h4>MAURIS ARCU TRISTIQUE URNA</h4><p>Lorem ipsum dolor sit amet, consectetur adipiscing elit interdum a imperdiet ultrices, velit magna faucibus.</p></div></div>
  <div class="post" style="left:615px;top:133px"><div class="ph" role="img" aria-label="Engineer with a tablet at an industrial plant" style="background:linear-gradient(135deg,#c5ccd2,#5a5e62)"></div><div class="tx"><div class="d">JANUARY 18, 2019</div><h4>MAURIS ARCU TRISTIQUE URNA</h4><p>Lorem ipsum dolor sit amet, consectetur adipiscing elit interdum a imperdiet ultrices, velit magna faucibus.</p></div></div>
  <div class="post" style="left:74px;top:310px"><div class="ph" role="img" aria-label="Offshore oil rig under a blue sky" style="background:linear-gradient(180deg,#3d74b8,#5f8fbf 55%,#1d4a78)"></div><div class="tx"><div class="d">JANUARY 18, 2019</div><h4>MAURIS ARCU TRISTIQUE URNA</h4><p>Lorem ipsum dolor sit amet, consectetur adipiscing elit interdum a imperdiet ultrices, velit magna faucibus.</p></div></div>
  <div class="post" style="left:615px;top:310px"><div class="ph" role="img" aria-label="Red drilling machine on rocky ground" style="background:linear-gradient(180deg,#4a78b3,#a8b7c4 50%,#5e5349)"></div><div class="tx"><div class="d">JANUARY 18, 2019</div><h4>MAURIS ARCU TRISTIQUE URNA</h4><p>Lorem ipsum dolor sit amet, consectetur adipiscing elit interdum a imperdiet ultrices, velit magna faucibus.</p></div></div>
</section>

<section class="reviews">
  <h2 class="h-title abs" style="top:68px">CUSTOMER <span>REVIEWS</span></h2>
  <svg class="abs" style="left:574px;top:138px" width="52" height="40" viewBox="0 0 52 40"><path fill="#3c5a2b" d="M0 0h22v20c0 10-6 18-16 20l-2-6c5-2 8-6 8-12H0zM30 0h22v20c0 10-6 18-16 20l-2-6c5-2 8-6 8-12H30z"/></svg>
  <p class="abs" style="left:160px;top:199px;width:880px;text-align:center;font-size:15px;line-height:27px">After days at sea, I really enjoy sitting in some coffeeshop, opening my computer and connecting with other Penwharf writers and work with words instead of ropes and sails. And more! With Penwharf, I have discovered some corners of the digital world that I would otherwise have never visited. So, even while working I keep traveling.</p>
  <svg class="abs" style="left:74px;top:260px" width="20" height="32" viewBox="0 0 20 32"><path d="M17 2L3 16l14 14" fill="none" stroke="#333" stroke-width="3"/></svg>
  <svg class="abs" style="left:1104px;top:260px" width="20" height="32" viewBox="0 0 20 32"><path d="M3 2l14 14L3 30" fill="none" stroke="#333" stroke-width="3"/></svg>
  <div class="person" style="left:374px"><div class="av" role="img" aria-label="Customer portrait"></div><h5>NAME HEADING</h5><small>Location</small></div>
  <div class="person" style="left:528px"><div class="av" role="img" aria-label="Customer portrait" style="border:4px solid var(--gold)"></div><h5>NAME HEADING</h5><small>Location</small></div>
  <div class="person" style="left:684px"><div class="av" role="img" aria-label="Customer portrait"></div><h5>NAME HEADING</h5><small>Location</small></div>
</section>

<section class="news">
  <div class="news-title abs">NEWSLETTER SIGN UP</div>
  <div class="abs" style="left:321px;top:24px;width:304px;height:40px;background:#fff;font-size:13px;color:#555;padding:12px 12px">Enter Email Address</div>
  <div class="abs" style="left:632px;top:24px;width:110px;height:40px;background:var(--gold);color:#fff;font-family:Montserrat,sans-serif;font-size:13px;font-weight:600;display:flex;align-items:center;justify-content:center">SIGN UP</div>
  <div class="social abs" style="left:870px;top:31px;gap:30px" aria-label="Social links"><i style="width:26px;height:26px"></i><i style="width:26px;height:26px"></i><i style="width:26px;height:26px"></i><i style="width:26px;height:26px"></i><i style="width:26px;height:26px"></i></div>
</section>

<footer class="foot">
  <div class="abs" style="left:79px;top:62px"><h6>SITE MAP</h6><ul><li>Home</li><li>About Us</li><li>Services</li><li>Projects</li><li>Blog</li><li>Contact Us</li></ul></div>
  <div class="abs" style="left:281px;top:62px"><h6>SERVICES</h6><ul><li>Praesent consectetur</li><li>Dapibus lobortis</li><li>Fusce gravida nibh</li><li>Interdum</li><li>Pulvinar miin</li><li>Efficitur leo</li></ul></div>
  <div class="brand abs" style="left:514px;top:110px;font-size:15px"><i style="width:18px;height:18px"></i>KVR GLOBALINKS</div>
  <div class="abs" style="left:811px;top:62px;width:330px">
    <h6>CONTACT INFO</h6>
    <div class="abs" style="left:0;top:36px;font-size:14px;line-height:23px;width:330px">
      <svg class="abs" style="left:0;top:4px" width="11" height="14" viewBox="0 0 12 16"><path fill="#ddd" d="M6 0a6 6 0 0 0-6 6c0 4.5 6 10 6 10s6-5.5 6-10a6 6 0 0 0-6-6zm0 8.5A2.5 2.5 0 1 1 6 3.5a2.5 2.5 0 0 1 0 5z"/></svg>
      <div style="padding-left:34px">Meridyen Caddesi<br>No: 8/21 Cankaya / ANKARA / TURKEY</div>
      <svg class="abs" style="left:0;top:62px" width="12" height="12" viewBox="0 0 24 24"><path fill="#ddd" d="M6.6 10.8a15 15 0 0 0 6.6 6.6l2.2-2.2c.3-.3.7-.4 1-.2 1.1.4 2.3.6 3.6.6.6 0 1 .4 1 1V20c0 .6-.4 1-1 1A17 17 0 0 1 3 4c0-.6.4-1 1-1h3.5c.6 0 1 .4 1 1 0 1.3.2 2.5.6 3.6.1.3 0 .7-.2 1z"/></svg>
      <div style="padding-left:34px;margin-top:12px;line-height:27px">+90 312 555 0140 &nbsp;, &nbsp;+90 312 555 0141<br>+90 312 555 0142</div>
      <svg class="abs" style="left:0;top:126px" width="13" height="10" viewBox="0 0 16 12"><path fill="#ddd" d="M0 0h16v12H0zM1 1l7 5 7-5"/></svg>
      <div style="padding-left:34px;margin-top:10px">info@kvrglobalinks.com</div>
      <div style="padding-left:34px;margin-top:12px">Map Location</div>
    </div>
  </div>
</footer>
<div class="copy abs" style="left:0;top:4456px;width:1200px">Copyright © 2020 CompanyName. All Right Reserved</div>

</body>
</html>
```